eBook-Cover für Thriller gesucht
An dieser Stelle ein großes Lob und vielen Dank an die Designerin Larosa. Auch das zweite Buchcover ist wieder überaus gelungen, eine ganz tolle Arbeit. Auch die angenehme Zusammenarbeit war mir, wie schon beim ersten Auftrag, eine Freude. Ebenso hervorzuheben ist die Schnelligkeit und Kreativität, mit der die Designerin auf Änderungswünsche reagiert. Als Auftraggeber gebe ich verdiente fünf Sterne und bin mit dem Ergebnis wirklich sehr zufrieden.
Zielgruppe
Ich bin Autor. Zielgruppe sind (anspruchsvolle) Leser/innen von Thrillern und Kriminalromanen im ebook-Bereich.
Aufgabenstellung
- Gesucht wird ein ebook-Cover für einen Thriller mit dem Titel 'Kaltgrund'
- Grobe Aufteilung siehe Skizzen
- Fokus des Covers liegt auf dem Buchtitel und dem Motiv ('Blauer Drachen')
- Hintergrund eher hell, Assoziation mit zarter Eisfläche mit angedeuteten Rissen vom Hauptmotiv ausgehend. Dadurch auch Tiefe und Dreidimensionalität. (Beispiel zum Hintergrund: 'Schattenfrist' von Heinrich Wendel, jedoch ohne Blut )
-Titelschrift groß, Stil 'gekratzt' bzw. 'gestrichelt', (Schriftart ähnlich wie Autorenname bei 'Die Schleuse' von Matthias Kolbe). Schrift groß und 'treppenförmig' neben dem Hauptmotiv angeordnet. Schriftfarbe schwarz/dunkelblau, ähnlich Hauptmotiv (Bsp.: 'Schwarzeid' von Heinrich Wendel)
Hauptmotiv ist der vom rechten Coverrand hineinragende 'Blaue Drachen' (Glaucus atlanticus, siehe hochgeladenes Beispielbild von Wissnetz)
- Schriftart von Autorenname und Genre eher klar
- eigene Detailvorschläge zur Optimierung des Ergebnisses möglich bzw. erwünscht

```html
<!DOCTYPE html>
<html lang="de">
<head>
<meta charset="utf-8">
<title>Kaltgrund – Konrad Velten</title>
<link rel="stylesheet" href="https://fonts.googleapis.com/css2?family=Oswald:wght@500&family=Rubik+Dirt&family=Roboto:wght@700&display=swap">
<style>
  :root {
    --ice-light: #8fd3ee;
    --ice-mid: #4fb0e0;
    --ice-deep: #1f7fcb;
    --title-ink: #14254a;
    --cover-white: #ffffff;
    --motif-deep: #1d2f8a;
    --motif-glow: #3c5fd8;
  }
  html, body {
    margin: 0;
    padding: 0;
    width: 776px;
    height: 1200px;
    overflow: hidden;
    background: #ffffff;
  }
  .cover {
    position: relative;
    width: 776px;
    height: 1200px;
    overflow: hidden;
    background:
      radial-gradient(ellipse 60% 45% at 75% 25%, rgba(31,127,203,0.55), transparent 70%),
      radial-gradient(ellipse 70% 50% at 20% 80%, rgba(143,211,238,0.7), transparent 70%),
      linear-gradient(160deg, var(--ice-light) 0%, var(--ice-mid) 45%, var(--ice-deep) 100%);
  }
  .author {
    position: absolute;
    top: 48px;
    left: 0;
    width: 100%;
    margin: 0;
    text-align: center;
    font-family: "Oswald", sans-serif;
    font-weight: 500;
    font-size: 58px;
    line-height: 1;
    letter-spacing: 0.52em;
    padding-left: 0.52em;
    box-sizing: border-box;
    color: var(--cover-white);
  }
  .motif {
    position: absolute;
    top: 140px;
    left: 330px;
    width: 446px;
    height: 550px;
  }
  .title {
    position: absolute;
    inset: 0;
    margin: 0;
    font-family: "Rubik Dirt", sans-serif;
    font-weight: 400;
    color: var(--title-ink);
    font-size: 178px;
    line-height: 1;
  }
  .title-step {
    position: absolute;
    display: block;
    transform: rotate(-4deg);
    transform-origin: left bottom;
    white-space: nowrap;
  }
  .title-step--one { left: 32px; top: 535px; }
  .title-step--two { left: 150px; top: 668px; }
  .title-step--three { left: 380px; top: 820px; font-size: 196px; }
  .genre {
    position: absolute;
    top: 1100px;
    left: 0;
    width: 100%;
    margin: 0;
    text-align: center;
    font-family: "Roboto", sans-serif;
    font-weight: 700;
    font-size: 38px;
    letter-spacing: 0.95em;
    padding-left: 0.95em;
    box-sizing: border-box;
    color: var(--cover-white);
  }
</style>
</head>
<body>
  <main class="cover">
    <p class="author">Konrad Velten</p>

    <svg class="motif" role="img" aria-label="Blauer Drachen (Glaucus atlanticus), der vom rechten Rand ins Bild ragt" viewBox="0 0 446 550">
      <defs>
        <radialGradient id="motifTone" cx="65%" cy="50%" r="50%">
          <stop offset="0%" stop-color="var(--motif-deep)" stop-opacity="0.85"/>
          <stop offset="55%" stop-color="var(--motif-glow)" stop-opacity="0.45"/>
          <stop offset="100%" stop-color="var(--motif-glow)" stop-opacity="0"/>
        </radialGradient>
      </defs>
      <rect width="446" height="550" fill="url(#motifTone)"/>
    </svg>

    <h1 class="title" aria-label="Kaltgrund">
      <span class="title-step title-step--one">KALT</span>
      <span class="title-step title-step--two">GRU</span>
      <span class="title-step title-step--three">ND</span>
    </h1>

    <p class="genre">THRILLER</p>
  </main>
</body>
</html>
```